Website Design for a holiday home letting busines

We require a redesign of our present website www.pinebrookstays.com. We want the website to stand out and look professional and clean to make holiday hunters want to book a caravan or lodge holiday with us. Our logo is red however we DO NOT want the website to be red. We want a natural colour scheme.

The final design should communicate that we are a professional company to book with.

On the home page we require;
Overview of company
Photo
Search box for holiday (check in)
Late Deals
Reviews
News

We would like the following pages designed; home page, available dates page, caravans page, content page.

The website should be responsive for smart phones. One website I do like is http://www.verdoliso.be/nl/

Target Market(s)

Families

Industry/Entity Type

Travel

Number of Pages Required

5+ page

Font styles to use
Serif

Requirements
Must have
• The project must be responsive for mobile phones and tablets.
• Ability to search for holiday home holidays
• We want a natural colour scheme.
Nice to have
• A style we like is http://www.verdoliso.be/nl/
Should not have
• Do not use red as a colour for the website. Our logo is red so this is the only time we want this used.

```html
<!DOCTYPE html>
<html lang="en">
<head>
<meta charset="utf-8">
<title>Pinebrook Stays – Holiday Rentals</title>
<link href="https://fonts.googleapis.com/css2?family=Oswald:wght@400;500;600&family=Open+Sans:wght@400;600;700&display=swap" rel="stylesheet">
<style>
:root{
  --teal:#1b97a6;
  --teal-dark:#137482;
  --navy:#1f2f3a;
  --green:#76b13a;
  --brand:#c8272d;
  --ink:#333;
  --muted:#777;
  --line:#e2e2e2;
  --paper:#fff;
  --soft:#f4f4f4;
  --foot:#2a2a2a;
  --foot-dark:#1c1c1c;
}
*{box-sizing:border-box;margin:0;padding:0}
html,body{width:1200px;height:2212px;overflow:hidden}
body{font-family:"Open Sans",Arial,sans-serif;color:var(--ink);background:var(--paper);font-size:13px}
.head-font{font-family:"Oswald",Arial,sans-serif}
.wrap{width:1080px;margin:0 auto;position:relative}

/* top bar */
.topbar{height:40px;background:var(--navy);color:#fff;font-size:13px}
.topbar .wrap{display:flex;justify-content:space-between;align-items:center;height:40px}
.topbar .item{display:flex;align-items:center;gap:8px}
.social{display:flex;gap:6px;margin-left:8px}
.social span{width:22px;height:22px;border-radius:50%;background:var(--teal);display:block}

/* header */
.header{height:80px;background:#fff;border-bottom:1px solid var(--line)}
.header .wrap{display:flex;justify-content:space-between;align-items:center;height:80px}
.logo{display:flex;align-items:center;gap:10px}
.logo .mark{width:34px;height:34px;background:var(--brand)}
.logo .name{font-family:"Oswald",sans-serif;font-weight:600;font-size:28px;color:var(--brand)}
.logo small{display:block;font-family:"Oswald",sans-serif;font-size:11px;color:var(--brand);font-weight:600;margin-top:-4px}
.nav{display:flex;gap:30px;font-family:"Oswald",sans-serif;font-size:15px;text-transform:none}
.nav a{color:var(--ink);text-decoration:none}
.nav a.active{color:var(--teal)}

/* hero */
.hero{height:380px;background:linear-gradient(180deg,#9fc3d8 0%,#c9d7c4 55%,#8aa26c 100%);position:relative}
.hero-copy{position:absolute;left:60px;top:100px;color:#fff}
.hero-copy h1{font-family:"Oswald",sans-serif;font-size:40px;font-weight:500;letter-spacing:.5px;text-shadow:0 1px 3px rgba(0,0,0,.35)}
.hero-copy p{font-family:"Oswald",sans-serif;font-size:22px;width:520px;line-height:1.25;margin-top:6px;text-shadow:0 1px 3px rgba(0,0,0,.35)}
.btn{display:inline-block;background:var(--teal);color:#fff;font-family:"Oswald",sans-serif;font-size:14px;padding:9px 18px;text-decoration:none}
.hero-copy .btn{margin-top:22px}
.dots{position:absolute;bottom:16px;left:50%;transform:translateX(-50%);display:flex;gap:8px}
.dots i{width:11px;height:11px;border-radius:50%;background:rgba(255,255,255,.6);display:block}
.dots i.on{background:#fff}

/* search */
.search{background:var(--teal);height:100px;color:#fff}
.search .wrap{padding-top:16px}
.search h2{font-family:"Oswald",sans-serif;font-weight:400;font-size:20px;display:flex;align-items:center;gap:10px}
.search form{display:flex;gap:12px;margin-top:10px}
.field{background:#fff;color:var(--muted);height:34px;font-size:12px;display:flex;align-items:center;padding:0 10px;justify-content:space-between}
.search .go{background:var(--navy);color:#fff;font-family:"Oswald",sans-serif;width:130px;justify-content:center;font-size:14px}

/* intro */
.intro{height:340px;padding-top:40px}
.intro .wrap{display:flex;gap:40px}
.intro-text{width:560px}
.intro h2{font-family:"Oswald",sans-serif;font-size:24px;font-weight:500;margin-bottom:14px}
.intro p{font-size:12.5px;line-height:1.6;color:#555;margin-bottom:10px}
.video{width:480px;height:250px;background:linear-gradient(135deg,#b7cfa6,#7c9b6a);position:relative}
.video .play{position:absolute;left:50%;top:50%;transform:translate(-50%,-50%);width:62px;height:44px;background:var(--teal);border-radius:8px;display:flex;align-items:center;justify-content:center}

/* section title */
.section-title{text-align:center;font-family:"Oswald",sans-serif;font-size:28px;font-weight:500;color:var(--ink);position:relative}
.section-title:after{content:"";display:block;width:60px;height:3px;background:var(--teal);margin:8px auto 0}

/* units */
.units{height:380px;padding-top:10px}
.grid4{display:grid;grid-template-columns:repeat(4,1fr);gap:20px;margin-top:26px}
.unit .photo{height:170px;background:linear-gradient(160deg,#d9e2e6,#a9b9a4);position:relative}
.tag{position:absolute;right:0;bottom:16px;background:var(--green);color:#fff;font-family:"Oswald",sans-serif;font-size:15px;padding:6px 14px}
.unit h3{font-family:"Oswald",sans-serif;font-size:16px;font-weight:500;margin-top:10px}
.unit .meta{font-size:11.5px;color:var(--muted);margin-top:4px;display:flex;justify-content:space-between}
.unit .specs{display:flex;gap:16px;font-size:11.5px;margin-top:8px;padding-top:8px;border-top:1px solid var(--line);color:#555}
.unit .specs b{color:var(--teal)}

/* late deals */
.deals{height:280px;background:var(--teal);padding-top:22px}
.deals .ribbon{display:block;width:220px;margin:0 auto;background:#fff;color:var(--teal);text-align:center;font-family:"Oswald",sans-serif;font-size:20px;padding:4px 0}
.deals .grid4{margin-top:20px}
.deal{background:#fff;padding:10px}
.deal .photo{height:88px;background:linear-gradient(160deg,#e3e6df,#b9c2b1)}
.deal h3{font-family:"Oswald",sans-serif;font-size:15px;font-weight:500;margin-top:8px}
.deal .date{font-size:11px;color:var(--muted)}
.deal .price{font-size:12px;margin-top:4px}
.deal .price b{color:var(--teal);font-size:14px}
.deal .price s{color:var(--muted)}
.deal .book{font-size:11px;color:var(--green);font-weight:700;margin-top:4px}

/* feeds */
.feeds{height:360px;padding-top:30px}
.feeds .wrap{display:grid;grid-template-columns:1.15fr 1fr 1fr;gap:34px}
.col-head{display:flex;justify-content:space-between;align-items:flex-end;border-bottom:2px solid var(--line);padding-bottom:6px;margin-bottom:12px}
.col-head h2{font-family:"Oswald",sans-serif;font-size:22px;font-weight:500}
.col-head span{font-size:11px;color:var(--muted)}
.review{margin-bottom:14px}
.review h4{font-size:12px;color:var(--teal)}
.review p{font-size:11px;color:#666;line-height:1.45}
.post{display:flex;gap:10px;margin-bottom:14px}
.post .thumb{width:64px;height:56px;background:linear-gradient(160deg,#cfd9cf,#9fb09a);flex:none}
.post p{font-size:11px;line-height:1.45;color:#555}
.post .when{color:var(--teal);font-size:11px;font-weight:600}
.feedbox{border:1px solid var(--line);padding:10px}
.feedbox .top{display:flex;gap:8px;align-items:center}
.feedbox .top i{width:44px;height:44px;background:var(--teal);display:block}
.feedbox .top b{font-size:12px}
.feedbox .top small{display:block;font-size:10px;color:var(--muted)}
.feedbox .like{font-size:10.5px;color:#666;margin:10px 0 8px}
.faces{display:grid;grid-template-columns:repeat(6,1fr);gap:5px}
.faces i{height:40px;background:#c7d3d6;display:block}
.faces i:nth-child(3n){background:#b5c4ae}
.faces i:nth-child(4n){background:#d7cfc0}

/* footer */
.footer{height:252px;background:var(--foot);color:#ccc}
.footer .wrap{display:grid;grid-template-columns:1.1fr 1fr 1.3fr;gap:30px;padding-top:22px;height:210px}
.footer h3{font-family:"Oswald",sans-serif;color:#fff;font-weight:400;font-size:17px;margin-bottom:12px}
.links{display:grid;grid-template-columns:1fr 1fr;gap:6px 20px;font-size:11.5px}
.links li{list-style:none}
.links li:before{content:"› ";color:var(--teal)}
.contact p{font-size:11.5px;line-height:1.7}
.news{display:flex;gap:20px}
.news p{font-size:11px;line-height:1.5;margin-bottom:10px}
.news .row{display:flex}
.news .row .in{flex:1;background:#fff;height:30px;color:#999;font-size:11px;padding:7px 8px}
.news .row .ok{background:var(--teal);color:#fff;font-family:"Oswald",sans-serif;padding:6px 12px}
.badge{width:84px;height:84px;border-radius:50%;background:var(--green);flex:none;border:5px solid #fff}
.copy{height:42px;background:var(--foot-dark);font-size:11px;color:#999}
.copy .wrap{display:flex;justify-content:space-between;align-items:center;height:42px}
</style>
</head>
<body>

<div class="topbar">
  <div class="wrap">
    <div class="item">
      <svg width="14" height="14" viewBox="0 0 24 24"><path fill="#fff" d="M6.6 10.8a15.1 15.1 0 006.6 6.6l2.2-2.2c.3-.3.7-.4 1-.2 1.1.4 2.3.6 3.6.6.6 0 1 .4 1 1V20c0 .6-.4 1-1 1A17 17 0 013 4c0-.6.4-1 1-1h3.5c.6 0 1 .4 1 1 0 1.3.2 2.5.6 3.6.1.3 0 .7-.2 1z"/></svg>
      Call Now : 01632 960 450
      <svg width="14" height="14" viewBox="0 0 24 24" style="margin-left:14px"><path fill="#fff" d="M2 5h20v14H2z" opacity=".9"/><path fill="#1f2f3a" d="M2 5l10 8 10-8v2l-10 8L2 7z"/></svg>
      hello@pinebrookstays.com
    </div>
    <div class="item">Contact with us on
      <div class="social"><span></span><span></span><span></span></div>
    </div>
  </div>
</div>

<header class="header">
  <div class="wrap">
    <div class="logo">
      <div class="mark"></div>
      <div><span class="name">Pinebrook Stays</span><small>at Alderwick Castle Holiday Park</small></div>
    </div>
    <nav class="nav">
      <a class="active" href="#">Home</a><a href="#">Caravans &amp; Lodges</a><a href="#">Payment Plans</a><a href="#">Alderwick Castle</a><a href="#">Local Attractions</a><a href="#">Contact Us</a>
    </nav>
  </div>
</header>

<section class="hero" role="img" aria-label="Family smiling outside a static caravan at the holiday park">
  <div class="hero-copy">
    <h1>PRIVATE HOLIDAY RENTALS</h1>
    <p>QUALITY LODGE &amp; CARAVAN HIRE AT ALDERWICK CASTLE HOLIDAY PARK. BOOK ONLINE TODAY!</p>
    <a class="btn" href="#">MORE DETAILS</a>
  </div>
  <div class="dots"><i class="on"></i><i></i><i></i></div>
</section>

<section class="search">
  <div class="wrap">
    <h2><svg width="18" height="18" viewBox="0 0 24 24"><circle cx="10" cy="10" r="7" fill="none" stroke="#fff" stroke-width="2.5"/><path d="M15 15l6 6" stroke="#fff" stroke-width="2.5"/></svg>SEARCH FACILITY</h2>
    <form>
      <div class="field" style="width:290px">Category <span>▾</span></div>
      <div class="field" style="width:270px">Caravan type <span>▾</span></div>
      <div class="field" style="width:180px">Date In <span>▦</span></div>
      <div class="field" style="width:180px">Date Out <span>▦</span></div>
      <div class="field go">Search</div>
    </form>
  </div>
</section>

<section class="intro">
  <div class="wrap">
    <div class="intro-text">
      <h2>NO DEPOSIT HOLIDAYS</h2>
      <p>Would you like to book a 2014 caravan or lodge holiday at Alderwick Castle Holiday Park and pay no deposit?</p>
      <p>We have flexible low-cost weekly and monthly payment plans available from as low as £15 per week for three adults. This means you can secure your holiday now, with no need for a large deposit, leaving your budget free for the things you enjoy most.</p>
      <p>Once you confirm your chosen dates and caravan, payments start within 31 days. You can spread the cost of your stay over the months in the run up to your arrival, and keep the full balance settled before you travel with complete peace of mind.</p>
      <p>If you have any questions about our no deposit holiday plans please contact us and we will be happy to help.</p>
    </div>
    <div class="video" role="img" aria-label="Video preview of the holiday park">
      <div class="play"><svg width="20" height="20" viewBox="0 0 20 20"><path d="M5 3l12 7-12 7z" fill="#fff"/></svg></div>
    </div>
  </div>
</section>

<section class="units">
  <div class="wrap">
    <h2 class="section-title">OUR CARAVANS AND LODGES</h2>
    <div class="grid4">
      <article class="unit"><div class="photo" role="img" aria-label="Caravan exterior"><span class="tag">Book Now</span></div><h3>THE KESTREL</h3><div class="meta"><span>Caravan type</span><span>Lodge</span></div><div class="specs"><span><b>6</b> Sleeps</span><span><b>3</b> Bedrooms</span></div></article>
      <article class="unit"><div class="photo" role="img" aria-label="Caravan exterior"><span class="tag">Book Now</span></div><h3>THE MARLOW</h3><div class="meta"><span>Caravan type</span><span>Caravan</span></div><div class="specs"><span><b>6</b> Sleeps</span><span><b>2</b> Bedrooms</span></div></article>
      <article class="unit"><div class="photo" role="img" aria-label="Caravan exterior"><span class="tag">Book Now</span></div><h3>THE ASHBY</h3><div class="meta"><span>Caravan type</span><span>Caravan</span></div><div class="specs"><span><b>8</b> Sleeps</span><span><b>3</b> Bedrooms</span></div></article>
      <article class="unit"><div class="photo" role="img" aria-label="Lodge exterior"><span class="tag">Book Now</span></div><h3>THE LINDEN</h3><div class="meta"><span>Caravan type</span><span>Lodge</span></div><div class="specs"><span><b>6</b> Sleeps</span><span><b>2</b> Bedrooms</span></div></article>
    </div>
  </div>
</section>

<section class="deals">
  <div class="wrap">
    <span class="ribbon">LATE DEALS</span>
    <div class="grid4">
      <article class="deal"><div class="photo" role="img" aria-label="Caravan lounge interior"></div><h3>THE HARBOUR</h3><p class="date">Friday 26 September 2014 (3 nights)</p><p class="price"><b>£250</b> <s>Was £300</s></p><p class="book">BOOK NOW FOR £250 ›</p></article>
      <article class="deal"><div class="photo" role="img" aria-label="Caravan lounge interior"></div><h3>THE ASHBY</h3><p class="date">Friday 26 September 2014 (3 nights)</p><p class="price"><b>£230</b> <s>Was £290</s></p><p class="book">BOOK NOW FOR £230 ›</p></article>
      <article class="deal"><div class="photo" role="img" aria-label="Caravan lounge interior"></div><h3>THE ASHBY</h3><p class="date">Monday 29 September 2014 (4 nights)</p><p class="price"><b>£240</b> <s>Was £310</s></p><p class="book">BOOK NOW FOR £240 ›</p></article>
      <article class="deal"><div class="photo" role="img" aria-label="Caravan lounge interior"></div><h3>THE HARBOUR</h3><p class="date">Monday 29 September 2014 (4 nights)</p><p class="price"><b>£260</b> <s>Was £320</s></p><p class="book">BOOK NOW FOR £260 ›</p></article>
    </div>
  </div>
</section>

<section class="feeds">
  <div class="wrap">
    <div>
      <div class="col-head"><h2>Latest Reviews</h2><span>View All</span></div>
      <div class="review"><h4>Helen Marsh — The Ashby</h4><p>Very clean as advised. Very good location with fantastic views over the lake. We all had an amazing time and will book again next year.</p></div>
      <div class="review"><h4>Carla Benton — The Harbour</h4><p>Very enjoyable. Brilliant service and the caravan was spotless. Good location near the entertainment.</p></div>
      <div class="review"><h4>Diane Ferris — The Kestrel</h4><p>Due to my daughter's disabilities we needed a lot of help and the lodge was perfect for her. Highly recommended to all families.</p></div>
    </div>
    <div>
      <div class="col-head"><h2>Blog Post</h2><span>View All</span></div>
      <div class="post"><div class="thumb" role="img" aria-label="Park photo"></div><div><p>Lorem ipsum dolor sit amet, consectetur adipiscing elit sed do eiusmod.</p><p class="when">26-Aug-2013</p></div></div>
      <div class="post"><div class="thumb" role="img" aria-label="Park photo"></div><div><p>Lorem ipsum dolor sit amet, consectetur adipiscing elit sed do eiusmod.</p><p class="when">26-Aug-2013</p></div></div>
      <div class="post"><div class="thumb" role="img" aria-label="Park photo"></div><div><p>Lorem ipsum dolor sit amet, consectetur adipiscing elit sed do eiusmod.</p><p class="when">26-Aug-2013</p></div></div>
    </div>
    <div>
      <div class="col-head"><h2>Social Feed</h2><span></span></div>
      <div class="feedbox">
        <div class="top"><i></i><div><b>Pinebrook Stays</b><small>Follow our page</small></div></div>
        <p class="like">1,245 people follow Pinebrook Stays</p>
        <div class="faces" role="img" aria-label="Follower profile pictures"><i></i><i></i><i></i><i></i><i></i><i></i><i></i><i></i><i></i><i></i><i></i><i></i></div>
      </div>
    </div>
  </div>
</section>

<footer class="footer">
  <div class="wrap">
    <div>
      <h3>Quick Links</h3>
      <ul class="links"><li>About us</li><li>Alderwick Castle</li><li>News</li><li>Local Attractions</li><li>Caravans &amp; Lodges</li><li>Booking Guide</li><li>2014 Holidays</li><li>Terms &amp; Conditions</li><li>2015 Holidays</li><li>Privacy Policy</li><li>Late Deals</li><li>Contact Us</li></ul>
    </div>
    <div class="contact">
      <h3>Contact Information</h3>
      <p><b style="color:#fff">Pinebrook Stays Ltd</b><br>Unit 4 Mill Lane, Harlow Road<br>Fernbridge, Westshire FB4 2QT<br>Tel: 01632 960 450<br>hello@pinebrookstays.com<br>www.pinebrookstays.com</p>
    </div>
    <div>
      <h3>Newsletter Signup</h3>
      <div class="news">
        <div>
          <p>Sign up for our latest offers and deals, straight to your inbox every month.</p>
          <div class="row"><span class="in">Email address</span><span class="ok">GO</span></div>
        </div>
        <div class="badge" role="img" aria-label="Guest rating award"></div>
      </div>
    </div>
  </div>
  <div class="copy"><div class="wrap"><span>© 2014 Pinebrook Stays. All rights reserved.</span><span>Terms · Privacy · Sitemap</span></div></div>
</footer>

</body>
</html>
```